Brivelo - a brand new platform for targetted offers

Hello there, art hive!
As a new business we want to build a mobile web site (that later will be converted to mobile app) that will allow our customer to find great offers in their area provided by our partners.
What we'd like to get from you is a design of several mobile web site pages (screens). For the color choice we were considering unobtrusive combination of white, black and one of the extra colors: purple, green (shades ranging from green apple to mint) or cherry red. Most of the pages will contain images (offers) made by partners with unpredictable color combinations, so our main design should stay minimalist enough to keep customers attention to these images. The pages (screens) are as follows.
1. Welcome screen
- Product logo image
- Short text to thank customers for their choice
- Checkbox with text to accept Terms and Conditions (with link to them)
- Button to continue that is grayed out before the checkbox above is checked
2. List of offers (main screen)
- Header: search bar + 2 icon buttons: location button and menu button
- Info box with a link to profile screen to indicate that authorization is recommended
- Offers: a list of images headed with partner's icon and name aligned left and timer (clock icon + time) aligned right
- Menu: as it's planned, when menu button is pressed, a hover menu from the right is open to display a list of available screens
3. Partner's details and offers
- Header: Partner's name and back button
- Partner's full width logo image
- Short description text of a partner company (up to, say, 500 characters)
- Contact buttons with appropriate icons: "visit their web page" button, call button, location button, like/dislike buttons
- List of their offers as full-width images
- Selected offer should, also, show an "open-down" box with description aligned left and a button to use the offer aligned right
4. Favorites
- Header: Back button, screen name, filter button to open a hover screen to filter by location and other fields
- List of favorite partners with their icon and name aligned left and buttons to "subscribe"/"unsubscribe" (one button) and remove from favorites aligned right
5. Blacklist
- Same as favorites, with just "subscribe"/"unsubscribe" omitted
6. History
- List of taken offers displayed same way as on main screen with actual usage date instead of time remaining
7. Profile
- Header: Back button and screen name
- Rows of inputs for customer to define her age, gender, etc and/or authenticate by Pingwall, Velto, etc.
8. Terms and Conitions
- Text of ToS
9. Language
- List of rows to choose a desired language
As this is our first try of ArtHive platform, please, don't hesitate to ask more questions or correct us on our order. If it feels like there are too many screens requested ahead, please, start with the first few with the intention to complete all of them when we choose you as a winner.
Thank you in advance for your cooperation!

```html
<!DOCTYPE html>
<html lang="en">
<head>
<meta charset="utf-8">
<title>Brivelo – mobile screens</title>
<link href="https://fonts.googleapis.com/css2?family=Open+Sans:wght@400;600;700&display=swap" rel="stylesheet">
<style>
:root{
  --green:#0cc46e;
  --page:#a9a9a9;
  --panel:#ececec;
  --card:#ffffff;
  --ink:#333333;
  --muted:#8a8a8a;
  --line:#d7d7d7;
  --dark:#3a3a3a;
  --darker:#555555;
  --navy:#3b5a9a;
}
*{box-sizing:border-box;margin:0;padding:0}
html,body{width:1158px;height:1200px;overflow:hidden;background:var(--page);font-family:"Open Sans",sans-serif;color:var(--ink)}
.board{position:absolute;left:0;top:0;width:1448px;height:1500px;transform:scale(.8);transform-origin:0 0;background:var(--page)}
.screen{position:absolute;width:331px;background:var(--panel);overflow:hidden}
.header{height:43px;background:var(--green);display:flex;align-items:center;padding:0 6px;gap:7px}
.logo{color:#fff;font-weight:700;font-size:23px;letter-spacing:.5px;flex:1}
.header.center .logo{text-align:center}
.search{width:98px;height:21px;background:#fff;display:flex;align-items:center;justify-content:space-between;padding:0 5px 0 9px;font-size:8px;color:#aaa}
.hbtn{width:21px;height:21px;background:#fff;display:flex;align-items:center;justify-content:center}
.footer{background:var(--green);height:76px;position:relative;text-align:center;color:#fff;font-size:7px;font-weight:600;padding-top:16px}
.socials{display:flex;justify-content:center;gap:8px;margin-top:9px}
.socials span{width:25px;height:25px;border-radius:50%;background:#fff;display:flex;align-items:center;justify-content:center}
.socials i{width:8px;height:8px;border-radius:50%;background:#777;display:block}
.title{color:var(--green);font-size:26px;font-weight:600;text-align:center}
.back{position:absolute;width:20px;height:20px;background:#fff;display:flex;align-items:center;justify-content:center}

/* welcome */
.hero{position:relative;height:597px;background:radial-gradient(circle at 75% 30%,#c8383a 0,#9c2426 22%,#6b5a5c 50%,#5a5a5c 75%,#4a4a4c 100%)}
.hero-text{position:absolute;left:0;right:0;top:190px;text-align:center;color:#fff}
.hero-text h1{font-size:55px;font-weight:700;line-height:1}
.hero-text p{font-size:16px;font-weight:600;line-height:24px;margin:22px 18px 0}
.hero-text hr{border:0;border-top:1px solid rgba(255,255,255,.6);margin:16px 31px 17px}
.continue{display:inline-flex;align-items:center;gap:4px;background:#fff;color:#777;font-size:14px;padding:0 15px;height:37px}
.accept{font-size:13px;margin-top:16px;display:flex;justify-content:center;align-items:center;gap:5px}
.accept b{width:10px;height:10px;background:#fff;display:block}

/* profile */
.profile-card{position:absolute;left:6px;top:116px;width:319px;height:479px;background:#fff;padding:28px 10px 0}
.avatar{width:117px;height:117px;border-radius:50%;background:#e8e8e8;margin:0 auto 24px;display:flex;align-items:center;justify-content:center}
.field{height:34px;border:1px solid var(--line);background:#f6f6f6;margin-bottom:13px;font-size:11px;color:#777;display:flex;align-items:center;justify-content:space-between;padding:0 14px}
.auth{height:34px;display:flex;align-items:center;font-size:12px;font-weight:600;margin-top:8px}
.auth .ico{width:34px;height:34px;display:flex;align-items:center;justify-content:center}
.auth .ico i{width:10px;height:10px;background:#fff;display:block}
.auth span{flex:1;text-align:center;padding-right:34px}
.auth.pingwall{background:var(--navy);color:#fff;margin-top:30px}
.auth.pingwall .ico{background:#2f4a82}
.auth.velto{background:#ececec;color:#444}
.auth.velto .ico{background:#555}

/* offers */
.userbar{height:75px;background:var(--dark);display:flex}
.userbar .info{flex:1;display:flex;align-items:center;padding-left:8px;gap:8px}
.face{width:51px;height:51px;border-radius:50%;background:linear-gradient(#d9c2aa,#8d7a6a);border:2px solid #fff}
.welcome{color:#fff;font-size:12px}
.welcome small{display:block;font-size:6px;color:#bbb;margin:2px 0 6px}
.stats{display:flex;gap:19px}
.stat{position:relative;width:16px;height:14px}
.stat b{position:absolute;top:-6px;right:-6px;width:11px;height:11px;border-radius:50%;background:var(--green);font-size:6px;color:#fff;text-align:center;line-height:11px}
.side{width:42px;background:var(--darker);display:flex;flex-direction:column}
.side span{flex:1;display:flex;align-items:center;justify-content:center}
.side span+span{border-top:1px solid #4a4a4a}
.offers .title{margin:26px 0 9px}
.offer{margin:0 6px 22px;background:#fff}
.offer .img{height:167px}
.offer .row{height:66px;display:flex}
.offer .who{flex:1;padding:12px 0 0 10px;border-right:1px solid #eee}
.brand{font-size:13px;font-weight:600;letter-spacing:1px;height:24px;display:flex;align-items:center;color:#222}
.brand.small{font-size:8px;letter-spacing:1.5px;color:#777}
.sub{font-size:11px;color:#333}
.timer{width:160px;display:flex;align-items:center;gap:5px;padding-left:12px}
.clock{width:26px;height:26px}
.digits{display:flex;align-items:flex-start;font-size:21px;color:#555;gap:3px}
.digits span{display:flex;flex-direction:column;align-items:center;line-height:22px}
.digits small{font-size:7px;line-height:8px}
.refresh{height:86px;display:flex;align-items:center;justify-content:center;margin-top:-22px}

/* menu overlay */
.shade{position:absolute;left:0;top:0;width:331px;height:716px;background:rgba(20,20,20,.62)}
.menu{position:absolute;left:38px;top:0;width:293px;height:716px;background:rgba(45,45,45,.88);padding:0 8px 0 7px}
.menu a{display:flex;justify-content:flex-end;align-items:center;gap:14px;height:77.6px;border-bottom:1px solid #5a5a5a;color:#ddd;font-size:18.5px;font-weight:600;text-decoration:none;padding-right:14px}
.menu a:first-child{color:#fff;height:100px;padding-top:24px}
.menu a:last-child{border-bottom:0}
.menu a i{width:8px;height:8px;border-radius:50%;background:#fff;display:block}
.close{position:absolute;right:6px;top:11px;width:21px;height:21px;background:#fff;display:flex;align-items:center;justify-content:center}

/* favorites */
.fav{position:absolute;left:6px;width:319px;height:104px;background:#fff;padding:14px 11px 0 10px}
.fav .brand{font-size:9px;height:22px;letter-spacing:.5px;color:#333}
.fav .sub{font-size:10.5px;margin:2px 0 8px}
.fav .btns{display:flex;justify-content:space-between}
.sub-btn{width:107px;height:27px;background:var(--green);color:#fff;font-size:12px;display:flex;align-items:center;gap:5px;padding-left:8px}
.rm-btn{width:107px;height:27px;background:#ececec;color:#666;font-size:7px;display:flex;align-items:center;justify-content:center}
</style>
</head>
<body>
<div class="board">

<!-- Welcome -->
<section class="screen" style="left:21px;top:21px;height:717px">
  <div class="header center"><div class="logo">BRIVELO</div></div>
  <div class="hero" role="img" aria-label="Red cubes printed with percent signs on a blurred grey background">
    <div class="hero-text">
      <h1>Thank You</h1>
      <p>Cras eget leo sed nunc hendrerit ultricies eu at nisl. Praesent iaculis faucibus urna sit amet lacinia.</p>
      <hr>
      <span class="continue">Continue <svg width="10" height="10" viewBox="0 0 10 10"><circle cx="5" cy="5" r="5" fill="#777"/><path d="M4 2.5 6.5 5 4 7.5" stroke="#fff" stroke-width="1.5" fill="none"/></svg></span>
      <div class="accept"><b></b>I accept Terms and Conditions</div>
    </div>
  </div>
  <footer class="footer">Copyright © 2018 Brivelo. &nbsp;All rights reserved.
    <div class="socials"><span><i></i></span><span><i></i></span><span><i></i></span><span><i></i></span><span><i></i></span></div>
  </footer>
</section>

<!-- Profile -->
<section class="screen" style="left:21px;top:762px;height:696px">
  <div class="header">
    <div class="logo">BRIVELO</div>
    <div class="search">Search <svg width="10" height="10" viewBox="0 0 10 10"><circle cx="4" cy="4" r="3" stroke="#333" stroke-width="1.5" fill="none"/><path d="M6.3 6.3 9 9" stroke="#333" stroke-width="1.6"/></svg></div>
    <div class="hbtn"><svg width="8" height="11" viewBox="0 0 8 11"><path d="M4 0a4 4 0 0 1 4 4c0 3-4 7-4 7S0 7 0 4a4 4 0 0 1 4-4z" fill="#333"/><circle cx="4" cy="4" r="1.4" fill="#fff"/></svg></div>
    <div class="hbtn"><svg width="10" height="9" viewBox="0 0 10 9"><path d="M0 1h10M0 4.5h10M0 8h10" stroke="#333" stroke-width="1.6"/></svg></div>
  </div>
  <div class="back" style="left:7px;top:74px"><svg width="10" height="10" viewBox="0 0 10 10"><path d="M9 5H2M5 1.5 1.5 5 5 8.5" stroke="#333" stroke-width="1.8" fill="none"/></svg></div>
  <div class="title" style="margin-top:26px">Profile</div>
  <div class="profile-card">
    <div class="avatar"><svg width="56" height="58" viewBox="0 0 56 58"><circle cx="28" cy="16" r="14" fill="#ccc"/><path d="M2 58v-8c0-12 10-18 26-18s26 6 26 18v8z" fill="#ccc"/></svg></div>
    <div class="field">Name</div>
    <div class="field">Gender <svg width="9" height="5"><path d="M0 0h9L4.5 5z" fill="#555"/></svg></div>
    <div class="field">Age <svg width="9" height="5"><path d="M0 0h9L4.5 5z" fill="#555"/></svg></div>
    <div class="field">Location <svg width="9" height="5"><path d="M0 0h9L4.5 5z" fill="#555"/></svg></div>
    <div class="auth pingwall"><div class="ico"><i></i></div><span>AUTHENTICATE BY PINGWALL</span></div>
    <div class="auth velto"><div class="ico"><i></i></div><span>AUTHENTICATE BY VELTO</span></div>
  </div>
  <footer class="footer" style="position:absolute;bottom:0;width:100%">Copyright © 2018 Brivelo. &nbsp;All rights reserved.
    <div class="socials"><span><i></i></span><span><i></i></span><span><i></i></span><span><i></i></span><span><i></i></span></div>
  </footer>
</section>

<!-- Offers (main) -->
<section class="screen offers" style="left:379px;top:21px;height:1344px">
  <div class="header">
    <div class="logo">BRIVELO</div>
    <div class="search">Search <svg width="10" height="10" viewBox="0 0 10 10"><circle cx="4" cy="4" r="3" stroke="#333" stroke-width="1.5" fill="none"/><path d="M6.3 6.3 9 9" stroke="#333" stroke-width="1.6"/></svg></div>
    <div class="hbtn"><svg width="8" height="11" viewBox="0 0 8 11"><path d="M4 0a4 4 0 0 1 4 4c0 3-4 7-4 7S0 7 0 4a4 4 0 0 1 4-4z" fill="#333"/><circle cx="4" cy="4" r="1.4" fill="#fff"/></svg></div>
    <div class="hbtn"><svg width="10" height="9" viewBox="0 0 10 9"><path d="M0 1h10M0 4.5h10M0 8h10" stroke="#333" stroke-width="1.6"/></svg></div>
  </div>
  <div class="userbar">
    <div class="info">
      <div class="face" role="img" aria-label="User profile photo"></div>
      <div class="welcome">Welcome, MarkHale<small>Vestibulum condimentum, risus ut posuere</small>
        <div class="stats">
          <div class="stat"><svg width="16" height="12"><rect width="16" height="12" fill="#bbb"/><path d="M0 0l8 6 8-6" stroke="#888" fill="none"/></svg><b>5</b></div>
          <div class="stat"><svg width="14" height="14" viewBox="0 0 14 14"><path d="M7 1c3 0 4 2 4 5v3l2 2H1l2-2V6c0-3 1-5 4-5zM5 12h4a2 2 0 0 1-4 0z" fill="#bbb"/></svg><b>8</b></div>
          <div class="stat"><svg width="16" height="14" viewBox="0 0 16 14"><path d="M8 14 1.5 7.5A4 4 0 0 1 8 2.5a4 4 0 0 1 6.5 5z" fill="#bbb"/></svg><b>12</b></div>
          <div class="stat"><svg width="16" height="14" viewBox="0 0 16 14"><circle cx="8" cy="4" r="3.5" fill="#bbb"/><path d="M1 14c0-5 3-6 7-6s7 1 7 6z" fill="#bbb"/></svg><b>2</b></div>
        </div>
      </div>
    </div>
    <div class="side">
      <span><svg width="14" height="14" viewBox="0 0 14 14"><circle cx="7" cy="7" r="5" fill="none" stroke="#aaa" stroke-width="3" stroke-dasharray="3 2"/><circle cx="7" cy="7" r="2" fill="#aaa"/></svg></span>
      <span><svg width="14" height="14" viewBox="0 0 14 14"><circle cx="7" cy="7" r="7" fill="#aaa"/><text x="7" y="11" font-size="10" text-anchor="middle" fill="#555" font-family="Open Sans" font-weight="700">?</text></svg></span>
    </div>
  </div>
  <div class="title">Offers</div>
  <article class="offer"><div class="img" role="img" aria-label="Man tying brown leather brogues" style="background:linear-gradient(160deg,#6d6a68,#3e3a38 55%,#8a5a3a)"></div>
    <div class="row"><div class="who"><div class="brand" style="font-size:10px">elena marsh</div><div class="sub">Pellentesque a imperdiet</div></div>
    <div class="timer"><svg class="clock" viewBox="0 0 26 26"><circle cx="13" cy="13" r="11.5" fill="none" stroke="#aaa" stroke-width="2.5"/><path d="M13 7v6H9" stroke="#aaa" stroke-width="2" fill="none"/></svg><div class="digits"><span>12<small>hrs</small></span>:<span>50<small>mnts</small></span>:<span>08<small>sec</small></span></div></div></div></article>
  <article class="offer"><div class="img" role="img" aria-label="Woman in a flowing red gown on seaside rocks at dusk" style="background:linear-gradient(180deg,#2f5fa8 0,#6a7fb0 40%,#c8323a 55%,#9a1a20 75%,#2a2a2e)"></div>
    <div class="row"><div class="who"><div class="brand">CORVIA</div><div class="sub">Aenean facilisis tincidunt</div></div>
    <div class="timer"><svg class="clock" viewBox="0 0 26 26"><circle cx="13" cy="13" r="11.5" fill="none" stroke="#aaa" stroke-width="2.5"/><path d="M13 7v6H9" stroke="#aaa" stroke-width="2" fill="none"/></svg><div class="digits"><span>15<small>hrs</small></span>:<span>24<small>mnts</small></span>:<span>35<small>sec</small></span></div></div></div></article>
  <article class="offer"><div class="img" role="img" aria-label="Four young people posing against a white brick wall" style="background:linear-gradient(180deg,#e4e4e4,#cfcfcf 70%,#7a7a7a)"></div>
    <div class="row"><div class="who"><div class="brand small">TALDOR ATELIER</div><div class="sub">Proin placerat dapibus</div></div>
    <div class="timer"><svg class="clock" viewBox="0 0 26 26"><circle cx="13" cy="13" r="11.5" fill="none" stroke="#aaa" stroke-width="2.5"/><path d="M13 7v6H9" stroke="#aaa" stroke-width="2" fill="none"/></svg><div class="digits"><span>18<small>hrs</small></span>:<span>02<small>mnts</small></span>:<span>37<small>sec</small></span></div></div></div></article>
  <article class="offer"><div class="img" role="img" aria-label="Three friends laughing on a sunny beach" style="background:linear-gradient(180deg,#9fb7c9,#d8c3a6 55%,#e8dccb)"></div>
    <div class="row"><div class="who"><div class="brand small">SUNROE WEAR</div><div class="sub">Fusce sollicitudin</div></div>
    <div class="timer"><svg class="clock" viewBox="0 0 26 26"><circle cx="13" cy="13" r="11.5" fill="none" stroke="#aaa" stroke-width="2.5"/><path d="M13 7v6H9" stroke="#aaa" stroke-width="2" fill="none"/></svg><div class="digits"><span>21<small>hrs</small></span>:<span>13<small>mnts</small></span>:<span>56<small>sec</small></span></div></div></div></article>
  <div class="refresh"><svg width="38" height="38" viewBox="0 0 38 38"><path d="M6 17a13 13 0 0 1 24-6" stroke="#444" stroke-width="5" fill="none"/><path d="M32 3v11H21z" fill="#444"/><path d="M32 21a13 13 0 0 1-24 6" stroke="#444" stroke-width="5" fill="none"/><path d="M6 35V24h11z" fill="#444"/></svg></div>
  <footer class="footer" style="position:absolute;bottom:0;width:100%">Copyright © 2018 Brivelo. &nbsp;All rights reserved.
    <div class="socials"><span><i></i></span><span><i></i></span><span><i></i></span><span><i></i></span><span><i></i></span></div>
  </footer>
</section>

<!-- Offers with menu open -->
<section class="screen offers" style="left:738px;top:21px;height:1344px">
  <div class="header">
    <div class="logo">BRIVELO</div>
    <div class="search">Search</div>
    <div class="hbtn"></div>
    <div class="hbtn"></div>
  </div>
  <div class="userbar">
    <div class="info">
      <div class="face" role="img" aria-label="User profile photo"></div>
      <div class="welcome">Welcome, MarkHale<small>Vestibulum condimentum, risus ut posuere</small></div>
    </div>
    <div class="side"><span></span><span></span></div>
  </div>
  <div class="title">Offers</div>
  <article class="offer"><div class="img" role="img" aria-label="Man tying brown leather brogues" style="background:linear-gradient(160deg,#6d6a68,#3e3a38 55%,#8a5a3a)"></div>
    <div class="row"><div class="who"><div class="brand" style="font-size:10px">elena marsh</div><div class="sub">Pellentesque a imperdiet</div></div>
    <div class="timer"><div class="digits"><span>12<small>hrs</small></span>:<span>50<small>mnts</small></span>:<span>08<small>sec</small></span></div></div></div></article>
  <article class="offer"><div class="img" role="img" aria-label="Woman in a flowing red gown on seaside rocks at dusk" style="background:linear-gradient(180deg,#2f5fa8 0,#6a7fb0 40%,#c8323a 55%,#9a1a20 75%,#2a2a2e)"></div>
    <div class="row"><div class="who"><div class="brand">CORVIA</div><div class="sub">Aenean facilisis tincidunt</div></div>
    <div class="timer"><div class="digits"><span>15<small>hrs</small></span>:<span>24<small>mnts</small></span>:<span>35<small>sec</small></span></div></div></div></article>
  <article class="offer"><div class="img" role="img" aria-label="Four young people posing against a white brick wall" style="background:linear-gradient(180deg,#e4e4e4,#cfcfcf 70%,#7a7a7a)"></div>
    <div class="row"><div class="who"><div class="brand small">TALDOR ATELIER</div><div class="sub">Proin placerat dapibus</div></div>
    <div class="timer"><svg class="clock" viewBox="0 0 26 26"><circle cx="13" cy="13" r="11.5" fill="none" stroke="#aaa" stroke-width="2.5"/><path d="M13 7v6H9" stroke="#aaa" stroke-width="2" fill="none"/></svg><div class="digits"><span>18<small>hrs</small></span>:<span>02<small>mnts</small></span>:<span>37<small>sec</small></span></div></div></div></article>
  <article class="offer"><div class="img" role="img" aria-label="Three friends laughing on a sunny beach" style="background:linear-gradient(180deg,#9fb7c9,#d8c3a6 55%,#e8dccb)"></div>
    <div class="row"><div class="who"><div class="brand small">SUNROE WEAR</div><div class="sub">Fusce sollicitudin</div></div>
    <div class="timer"><svg class="clock" viewBox="0 0 26 26"><circle cx="13" cy="13" r="11.5" fill="none" stroke="#aaa" stroke-width="2.5"/><path d="M13 7v6H9" stroke="#aaa" stroke-width="2" fill="none"/></svg><div class="digits"><span>21<small>hrs</small></span>:<span>13<small>mnts</small></span>:<span>56<small>sec</small></span></div></div></div></article>
  <div class="refresh"><svg width="38" height="38" viewBox="0 0 38 38"><path d="M6 17a13 13 0 0 1 24-6" stroke="#444" stroke-width="5" fill="none"/><path d="M32 3v11H21z" fill="#444"/><path d="M32 21a13 13 0 0 1-24 6" stroke="#444" stroke-width="5" fill="none"/><path d="M6 35V24h11z" fill="#444"/></svg></div>
  <footer class="footer" style="position:absolute;bottom:0;width:100%">Copyright © 2018 Brivelo. &nbsp;All rights reserved.
    <div class="socials"><span><i></i></span><span><i></i></span><span><i></i></span><span><i></i></span><span><i></i></span></div>
  </footer>
  <div class="shade"></div>
  <nav class="menu">
    <a>WELCOME <i></i></a><a>OFFERS <i></i></a><a>PARTNERS <i></i></a><a>FAVORITES <i></i></a><a>BLACKLIST <i></i></a><a>HISTORY <i></i></a><a>PROFILE <i></i></a><a>TERMS AND CONDITIONS <i></i></a><a>LANGUAGE <i></i></a>
  </nav>
  <div class="close"><svg width="12" height="12" viewBox="0 0 12 12"><circle cx="6" cy="6" r="6" fill="#333"/><path d="M3.8 3.8l4.4 4.4M8.2 3.8 3.8 8.2" stroke="#fff" stroke-width="1.5"/></svg></div>
</section>

<!-- Favorites -->
<section class="screen" style="left:1096px;top:21px;height:1105px">
  <div class="header">
    <div class="logo">BRIVELO</div>
    <div class="search">Search <svg width="10" height="10" viewBox="0 0 10 10"><circle cx="4" cy="4" r="3" stroke="#333" stroke-width="1.5" fill="none"/><path d="M6.3 6.3 9 9" stroke="#333" stroke-width="1.6"/></svg></div>
    <div class="hbtn"><svg width="8" height="11" viewBox="0 0 8 11"><path d="M4 0a4 4 0 0 1 4 4c0 3-4 7-4 7S0 7 0 4a4 4 0 0 1 4-4z" fill="#333"/><circle cx="4" cy="4" r="1.4" fill="#fff"/></svg></div>
    <div class="hbtn"><svg width="10" height="9" viewBox="0 0 10 9"><path d="M0 1h10M0 4.5h10M0 8h10" stroke="#333" stroke-width="1.6"/></svg></div>
  </div>
  <div class="back" style="left:7px;top:73px"><svg width="10" height="10" viewBox="0 0 10 10"><path d="M9 5H2M5 1.5 1.5 5 5 8.5" stroke="#333" stroke-width="1.8" fill="none"/></svg></div>
  <div class="back" style="right:7px;top:73px"><svg width="10" height="10" viewBox="0 0 10 10"><path d="M0 1h10L6 5.5V10L4 9V5.5z" fill="#333"/></svg></div>
  <div class="title" style="margin-top:25px">Favorites</div>

  <div class="fav" style="top:115px"><div class="brand">LOOMARA</div><div class="sub">Aliquam consectetur</div><div class="btns"><span class="sub-btn"><svg width="10" height="10" viewBox="0 0 10 10"><circle cx="1.5" cy="8.5" r="1.5" fill="#fff"/><path d="M0 4.5A5.5 5.5 0 0 1 5.5 10M0 1a9 9 0 0 1 9 9" stroke="#fff" stroke-width="1.6" fill="none"/></svg>Unsubscribe</span><span class="rm-btn">Remove from favorites</span></div></div>
  <div class="fav" style="top:229px"><div class="brand">IVY BRANDT</div><div class="sub">Vestibulum condimentum</div><div class="btns"><span class="sub-btn"><svg width="10" height="10" viewBox="0 0 10 10"><circle cx="1.5" cy="8.5" r="1.5" fill="#fff"/><path d="M0 4.5A5.5 5.5 0 0 1 5.5 10M0 1a9 9 0 0 1 9 9" stroke="#fff" stroke-width="1.6" fill="none"/></svg>Unsubscribe</span><span class="rm-btn">Remove from favorites</span></div></div>
  <div class="fav" style="top:343px"><div class="brand">Norell Denim</div><div class="sub">Proin eget congue</div><div class="btns"><span class="sub-btn"><svg width="10" height="10" viewBox="0 0 10 10"><circle cx="1.5" cy="8.5" r="1.5" fill="#fff"/><path d="M0 4.5A5.5 5.5 0 0 1 5.5 10M0 1a9 9 0 0 1 9 9" stroke="#fff" stroke-width="1.6" fill="none"/></svg>Unsubscribe</span><span class="rm-btn">Remove from favorites</span></div></div>
  <div class="fav" style="top:457px"><div class="brand">HARLOW &amp; CO</div><div class="sub">Aliquam erat volutpat</div><div class="btns"><span class="sub-btn"><svg width="10" height="10" viewBox="0 0 10 10"><circle cx="1.5" cy="8.5" r="1.5" fill="#fff"/><path d="M0 4.5A5.5 5.5 0 0 1 5.5 10M0 1a9 9 0 0 1 9 9" stroke="#fff" stroke-width="1.6" fill="none"/></svg>Subscribe</span><span class="rm-btn">Remove from favorites</span></div></div>
  <div class="fav" style="top:571px"><div class="brand">Solvane</div><div class="sub">Quisque aliquet ex</div><div class="btns"><span class="sub-btn"><svg width="10" height="10" viewBox="0 0 10 10"><circle cx="1.5" cy="8.5" r="1.5" fill="#fff"/><path d="M0 4.5A5.5 5.5 0 0 1 5.5 10M0 1a9 9 0 0 1 9 9" stroke="#fff" stroke-width="1.6" fill="none"/></svg>Unsubscribe</span><span class="rm-btn">Remove from favorites</span></div></div>
  <div class="fav" style="top:685px"><div class="brand">Alder Peak</div><div class="sub">Pellentesque convallis</div><div class="btns"><span class="sub-btn"><svg width="10" height="10" viewBox="0 0 10 10"><circle cx="1.5" cy="8.5" r="1.5" fill="#fff"/><path d="M0 4.5A5.5 5.5 0 0 1 5.5 10M0 1a9 9 0 0 1 9 9" stroke="#fff" stroke-width="1.6" fill="none"/></svg>Subscribe</span><span class="rm-btn">Remove from favorites</span></div></div>
  <div class="fav" style="top:799px"><div class="brand">WAVECREST</div><div class="sub">Etiam id imperdiet</div><div class="btns"><span class="sub-btn"><svg width="10" height="10" viewBox="0 0 10 10"><circle cx="1.5" cy="8.5" r="1.5" fill="#fff"/><path d="M0 4.5A5.5 5.5 0 0 1 5.5 10M0 1a9 9 0 0 1 9 9" stroke="#fff" stroke-width="1.6" fill="none"/></svg>Unsubscribe</span><span class="rm-btn">Remove from favorites</span></div></div>
  <div class="fav" style="top:913px"><div class="brand" style="font-size:13px;font-weight:400">MERIDIAN</div><div class="sub">Aliquam consectetur</div><div class="btns"><span class="sub-btn"><svg width="10" height="10" viewBox="0 0 10 10"><circle cx="1.5" cy="8.5" r="1.5" fill="#fff"/><path d="M0 4.5A5.5 5.5 0 0 1 5.5 10M0 1a9 9 0 0 1 9 9" stroke="#fff" stroke-width="1.6" fill="none"/></svg>Unsubscribe</span><span class="rm-btn">Remove from favorites</span></div></div>

  <footer class="footer" style="position:absolute;bottom:0;width:100%">Copyright © 2018 Brivelo. &nbsp;All rights reserved.
    <div class="socials"><span><i></i></span><span><i></i></span><span><i></i></span><span><i></i></span><span><i></i></span></div>
  </footer>
</section>

</div>
</body>
</html>
```